Business Card Design for Online Gift Business

Business card design for a new online Canadian company called "Harlow & Brine Gift Boxes" selling modern and luxurious gift boxes for every occasion. Items are sourced locally from talented socially-responsible Canadian artisans. Each gift is elegantly presented in a keepsake wood box to ensure a lasting impression.

Industry/Entity Type

E-Commerce

Contact Information for Business Card

Marla Whitcombe, Proprietor
Kelowna, BC
403-555-2741
www.harlowandbrine.ca
hello@harlowandbrine.ca

Requirements
Must have
• Chosen with care, given with love
• Please also include the symbols for Facebook and Instagram
Nice to have
• **I have attached a few samples of background colors and font colors that I like. I hope this helps in a few directions to try.

```html
<!DOCTYPE html>
<html lang="en">
<head>
<meta charset="utf-8">
<title>Harlow &amp; Brine Gift Boxes — Business Card</title>
<link rel="stylesheet" href="https://fonts.googleapis.com/css2?family=EB+Garamond:ital,wght@0,400;0,500;1,600&display=swap">
<style>
  :root {
    --backdrop: #a7b2b1;
    --card: #efebe8;
    --ink: #2b2523;
    --frame: #231e1c;
    --shadow: rgba(40, 50, 50, 0.28);
  }
  * { box-sizing: border-box; margin: 0; padding: 0; }
  html, body {
    width: 1200px;
    height: 824px;
    overflow: hidden;
    background: var(--backdrop);
  }
  .canvas {
    position: relative;
    width: 1200px;
    height: 824px;
    display: flex;
    align-items: center;
    justify-content: center;
    gap: 40px;
  }
  .card {
    position: relative;
    width: 540px;
    height: 309px;
    background: var(--card);
    box-shadow: 0 10px 24px var(--shadow);
    color: var(--ink);
    font-family: "EB Garamond", Georgia, serif;
  }
  .card__frame {
    position: absolute;
    inset: 16px;
    border: 2.5px solid var(--frame);
  }

  /* Contact side */
  .contact {
    position: absolute;
    inset: 0;
    display: flex;
    flex-direction: column;
    align-items: center;
    justify-content: center;
    text-align: center;
    text-transform: uppercase;
  }
  .contact__name {
    font-size: 27px;
    font-weight: 400;
    letter-spacing: 0.02em;
    line-height: 1.1;
  }
  .contact__role {
    display: flex;
    align-items: center;
    gap: 8px;
    font-size: 15px;
    letter-spacing: 0.04em;
    margin: 2px 0 6px;
  }
  .contact__rule {
    width: 30px;
    height: 1px;
    background: var(--ink);
  }
  .contact__line {
    font-size: 16.5px;
    line-height: 1.22;
    letter-spacing: 0.01em;
  }
  .contact__social {
    display: flex;
    gap: 6px;
    margin-top: 6px;
  }
  .contact__social-mark {
    width: 17px;
    height: 17px;
    border: 1.3px solid var(--ink);
    border-radius: 50%;
  }

  /* Brand side */
  .brand {
    position: absolute;
    inset: 0;
    display: flex;
    flex-direction: column;
    align-items: center;
    justify-content: center;
    gap: 22px;
  }
  .brand__name {
    display: flex;
    align-items: center;
    gap: 12px;
    font-size: 46px;
    font-weight: 400;
    letter-spacing: 0.04em;
    line-height: 1;
  }
  .brand__dot {
    width: 14px;
    height: 14px;
    border-radius: 50%;
    background: var(--ink);
  }
  .brand__tagline {
    font-size: 22px;
    font-style: italic;
    font-weight: 600;
  }
</style>
</head>
<body>
  <main class="canvas">
    <section class="card card--contact" aria-label="Contact side">
      <div class="card__frame"></div>
      <div class="contact">
        <h1 class="contact__name">Marla Whitcombe</h1>
        <p class="contact__role">
          <span class="contact__rule"></span>
          Proprietor
          <span class="contact__rule"></span>
        </p>
        <p class="contact__line">Kelowna, BC</p>
        <p class="contact__line">www.harlowandbrine.ca</p>
        <p class="contact__line">403-555-2741</p>
        <div class="contact__social" aria-label="Social media">
          <span class="contact__social-mark"></span>
          <span class="contact__social-mark"></span>
        </div>
      </div>
    </section>

    <section class="card card--brand" aria-label="Brand side">
      <div class="card__frame"></div>
      <div class="brand">
        <p class="brand__name"><span class="brand__dot"></span>Harlow &amp; Brine</p>
        <p class="brand__tagline">Chosen with care, given with love</p>
      </div>
    </section>
  </main>
</body>
</html>
```